Natural healthcare clinic needs stationery and business card design

We have had a logo developed by Pixel Harbor and are now looking at utilising it for a new business concept. The concept is a natural healthcare clinic that hosts a number of small businesses. The individual practitioners may want to utilise the host business stationery to provide a consistent message to clients.

I am looking for a stationery design - letterhead, DL brochure template and business card that uses our logo. The business name 'Bright Meadows' is all about getting rhythm back into your life so you can be fit and healthy. The stationery design should reflect this.

There are a couple of requirements for the business card, it needs to be double-sided with black and white back. There should be lines to write appointment times on. The cards may need to be custom named on the front for example Carol Fenwick, Remedial Therapist and Aromatherapist. Therefore if a template can be provided so we can customise this information using MS Publisher, it would be appreciated.

The DL brochure template needs to be A4 folded to DL. I am looking for a consistent brand message that can be utilised to produce our own clinic brochures.

The natural healthcare clinic will host the following types of businesses - remedial massage, pregnancy massage, oncology massage, aromatherapy, acupuncture - as a bit of a guide.

Target Market(s)

25-45 year old male and females who work full time.

Industry/Entity Type

Healthcare

Requirements
Must have
• Use the logo I have already.

```html
<!DOCTYPE html>
<html lang="en">
<head>
<meta charset="utf-8">
<title>Bright Meadows – Stationery Set</title>
<link rel="stylesheet" href="https://fonts.googleapis.com/css2?family=Open+Sans:wght@400;600;700&family=Roboto+Condensed:wght@700&display=swap">
<style>
:root{
  --backdrop:#e8e5e0;
  --green:#8aab2b;
  --green-deep:#6c931f;
  --brown:#6b5a27;
  --brown-text:#5c4a1e;
  --tab:#d9d9d9;
  --ink:#333;
  --muted:#555;
  --red:#ee1c25;
  --blue:#2b3990;
  --paper:#fff;
  --line:#7fc25a;
}
*{box-sizing:border-box;margin:0;padding:0}
html,body{width:1200px;height:963px;overflow:hidden;background:var(--backdrop)}
body{font-family:"Open Sans",Arial,sans-serif;color:var(--ink)}
.stage{position:relative;width:1200px;height:963px;overflow:hidden}
.label{position:absolute;font-weight:700;font-size:20px;color:var(--ink)}
.caption{position:absolute;font-size:10px;color:var(--ink)}
.sheet{position:absolute;background:var(--paper);box-shadow:0 2px 6px rgba(0,0,0,.25);overflow:hidden}
.brand-name{font-family:"Open Sans",Arial,sans-serif;font-weight:600;color:var(--brown-text);white-space:nowrap;display:flex;align-items:center;gap:6px}
.brand-name .dot{width:.55em;height:.55em;border-radius:50%;background:var(--green)}
.swoosh{position:absolute;left:0;bottom:0;display:block}

/* letterhead */
.letterhead{left:51px;top:77px;width:514px;height:664px}
.letterhead .brand-name{position:absolute;left:30px;top:110px;font-size:26px}
.letterhead-footer{position:absolute;left:0;bottom:0;width:514px;height:130px}
.contact-list{position:absolute;left:32px;bottom:20px;list-style:none;color:#fff;font-size:9.5px;line-height:14px}
.contact-list li{display:flex;align-items:center;gap:6px}
.contact-list svg{width:9px;height:9px;fill:#fff}
.clinic-block{position:absolute;left:182px;bottom:20px;color:#fff}
.clinic-block h3{font-size:15px;font-weight:600}
.clinic-block p{font-size:8.5px;margin-top:8px}

/* brochure */
.panel{top:78px;width:251px;height:708px}
.panel-services{left:597px;background:linear-gradient(180deg,#8fb02e,#6c931f 75%);color:#fff}
.panel-services h2{font-size:18.5px;font-weight:600;line-height:26px;padding:16px 0 0 19px}
.service{margin-top:13px}
.service-tab{display:inline-block;position:relative;background:linear-gradient(90deg,#c8c8c8,#ececec);color:var(--ink);font-size:12.5px;font-weight:600;padding:2px 22px 2px 19px;clip-path:polygon(0 0,92% 0,100% 50%,92% 100%,0 100%);width:170px}
.service p{font-size:6.6px;line-height:9.4px;padding:6px 14px 0 19px;text-align:justify}
.panel-services .promo{font-size:13px;font-weight:700;line-height:18px;padding:20px 14px 0 17px}
.panel-services .call{font-size:14px;padding:16px 0 0 19px;display:flex;align-items:baseline;gap:6px}
.panel-services .call strong{font-family:"Roboto Condensed",Arial,sans-serif;font-size:24px}
.panel-services .web{font-family:"Roboto Condensed",Arial,sans-serif;font-size:13px;letter-spacing:1.5px;padding:2px 0 0 19px}
.panel-foot{position:absolute;left:0;bottom:0;width:251px;height:182px;background:#fff}
.panel-foot .brand-name{position:absolute;left:14px;top:34px;font-size:11px}
.panel-foot .tag{position:absolute;left:14px;top:52px;font-size:5.5px;color:var(--muted)}
.photo{position:absolute;background:linear-gradient(135deg,#e9d0bd,#c9a184 55%,#8f6a50)}
.panel-services .photo{left:0;bottom:0;width:251px;height:118px;background:linear-gradient(120deg,#f3e3d6,#d8b49a 50%,#b98e70)}

.panel-intro{left:863px;background:linear-gradient(180deg,#ffffff,#e9e9e9)}
.intro-head{position:relative;height:190px;color:#fff;text-align:center}
.intro-head svg{position:absolute;left:0;top:0}
.intro-head h2{position:relative;font-size:21px;font-weight:600;line-height:27px;padding-top:14px}
.intro-head p{position:relative;font-size:11.5px;font-weight:600;line-height:17px;padding:12px 18px 0}
.panel-intro .brand-name{position:absolute;left:14px;top:284px;font-size:25px}
.panel-intro .sub{position:absolute;left:15px;top:318px;font-size:11px;color:var(--muted)}
.panel-intro .body{position:absolute;left:15px;top:345px;width:222px;font-size:8px;line-height:12px;text-align:justify;color:var(--muted)}
.panel-intro .call{position:absolute;left:33px;top:412px;font-size:13px;color:var(--muted);display:flex;align-items:baseline;gap:6px}
.panel-intro .call strong{font-family:"Roboto Condensed",Arial,sans-serif;font-size:22px;color:var(--red)}
.panel-intro .web{position:absolute;left:35px;top:440px;font-family:"Roboto Condensed",Arial,sans-serif;font-size:13.5px;letter-spacing:.8px;color:var(--blue)}
.panel-intro .addr{position:absolute;left:0;width:251px;top:464px;text-align:center;font-size:7.5px;line-height:12px;color:var(--muted)}
.panel-intro .photo{left:0;bottom:0;width:251px;height:140px;background:linear-gradient(120deg,#d9b8a4,#a45a48 55%,#7a2b24)}

/* cards */
.card{width:213px;height:121px;background:linear-gradient(180deg,#fff,#e7e7e7)}
.card-front{left:51px;top:781px}
.card-front .brand-name{position:absolute;left:10px;top:52px;font-size:12px}
.card-divider{position:absolute;left:117px;top:8px;width:1px;height:68px;background:#bbb}
.card-person{position:absolute;left:130px;top:10px;color:var(--muted)}
.card-person h4{font-size:9px;font-weight:600}
.card-person .role{font-size:5.5px;letter-spacing:1px}
.card-person ul{list-style:none;font-size:5px;line-height:7px;margin-top:6px}
.card-band-text{position:absolute;color:#fff;font-weight:600}
.card-back-one{left:274px;top:781px}
.card-back-two{left:520px;top:806px}
.write-lines{position:absolute;left:34%;width:160px}
.write-lines span{display:block;height:1px;background:var(--line);margin-bottom:13px}
</style>
</head>
<body>
<div class="stage">

  <div class="label" style="left:51px;top:34px">Letterhead option 7</div>
  <div class="label" style="left:774px;top:34px">brochure option 7</div>

  <!-- Letterhead -->
  <section class="sheet letterhead" aria-label="Letterhead">
    <div class="brand-name"><span class="dot"></span>Bright Meadows</div>
    <div class="letterhead-footer">
      <svg class="swoosh" width="514" height="130" viewBox="0 0 514 130">
        <path d="M0 38 C200 24 390 52 495 130 L0 130 Z" fill="var(--green)"/>
        <path d="M0 10 C220 0 410 36 514 118 L514 126 C400 56 220 22 0 28 Z" fill="var(--brown)"/>
      </svg>
      <ul class="contact-list">
        <li><svg viewBox="0 0 10 10"><path d="M2 0h2l1 3-1.5 1a6 6 0 0 0 2.5 2.5L7 5l3 1v2c0 1-1 2-2 2A8 8 0 0 1 0 2c0-1 1-2 2-2z"/></svg>012.345.6789</li>
        <li><svg viewBox="0 0 10 10"><path d="M0 2h10v6H0z M0 2l5 3 5-3" stroke="#7a9a25" stroke-width=".8"/></svg>info@brightmeadows.com</li>
        <li><svg viewBox="0 0 10 10"><circle cx="5" cy="5" r="5"/></svg>www.brightmeadows.com</li>
      </ul>
      <div class="clinic-block">
        <h3>Well Being Clinic</h3>
        <p>Suite 000, City name, Country name 00000</p>
      </div>
    </div>
  </section>

  <!-- Brochure inner panel -->
  <section class="sheet panel panel-services" aria-label="Brochure services panel">
    <h2>Lorem Ipsum Dolor sit<br>Consectetur adipisicing</h2>
    <div class="service" style="margin-top:12px">
      <span class="service-tab">Remedial Massage</span>
      <p>Lorem ipsum dolor sit amet, consectetur adipisicing elit, sed do eiusmod tempor incididunt ut labore et dolore magna aliqua. Ut enim ad minim veniam, quis nostrud exercitation ullamco laboris nisi ut aliquip ex ea commodo consequat. Duis aute irure dolor in reprehenderit in voluptate velit esse cillum dolore eu fugiat nulla pariatur.</p>
    </div>
    <div class="service">
      <span class="service-tab">Pregnancy Massage</span>
      <p>Lorem ipsum dolor sit amet, consectetur adipisicing elit, sed do eiusmod tempor incididunt ut labore et dolore magna aliqua. Ut enim ad minim veniam, quis nostrud exercitation ullamco laboris nisi ut aliquip ex ea commodo consequat. Duis aute irure dolor in reprehenderit in voluptate velit esse cillum dolore eu fugiat nulla pariatur. Excepteur sint occaecat cupidatat non proident.</p>
    </div>
    <div class="service">
      <span class="service-tab">Oncology Massage</span>
      <p>Lorem ipsum dolor sit amet, consectetur adipisicing elit, sed do eiusmod tempor incididunt ut labore et dolore magna aliqua. Ut enim ad minim veniam, quis nostrud exercitation ullamco laboris nisi ut aliquip ex ea commodo consequat. Duis aute irure dolor in reprehenderit in voluptate velit esse cillum dolore eu fugiat nulla pariatur. Excepteur sint occaecat cupidatat non proident, sunt in culpa qui officia deserunt mollit anim id est laborum.</p>
    </div>
    <p class="promo">Lorem Ipsum dolor sit amet do consectetur adipisicing elit do sed.</p>
    <p class="call">Call Us: <strong>012.345.6789</strong></p>
    <p class="web">www.brightmeadows.com</p>
    <div class="panel-foot">
      <svg class="swoosh" width="251" height="182" viewBox="0 0 251 182" style="top:0;bottom:auto">
        <path d="M0 8 C110 -6 210 20 251 70 L251 78 C200 30 110 10 0 20 Z" fill="var(--brown)"/>
        <path d="M0 0 L251 0 L251 40 C200 10 110 -2 0 4 Z" fill="var(--green-deep)"/>
        <path d="M120 40 C180 40 230 60 251 90 L251 64 C220 40 180 32 120 40 Z" fill="var(--green)"/>
      </svg>
      <div class="brand-name"><span class="dot"></span>Bright Meadows</div>
      <div class="tag">Well Being Clinic</div>
      <div class="photo" role="img" aria-label="Photo of a therapist massaging a relaxed client"></div>
    </div>
  </section>

  <!-- Brochure cover panel -->
  <section class="sheet panel panel-intro" aria-label="Brochure cover panel">
    <div class="intro-head">
      <svg width="251" height="190" viewBox="0 0 251 190">
        <path d="M0 0 H251 V148 C180 128 90 124 0 148 Z" fill="var(--brown)"/>
        <path d="M20 162 C110 120 200 130 251 158 L251 188 C200 156 110 144 20 162 Z" fill="var(--green)"/>
      </svg>
      <h2>LOREM<br>IPSUM DOLOR SIT</h2>
      <p>Carol Fenwick, Remedial Massage Pregnancy Massage, Oncology Massage, Aromatherapy, Acupuncture</p>
    </div>
    <div class="brand-name"><span class="dot"></span>Bright Meadows</div>
    <div class="sub">Well Being Clinic</div>
    <p class="body">Lorem ipsum dolor sit amet, consectetur adipisicing elit, sed do eiusmod tempor incididunt ut labore et dolore magna aliqua. Ut enim ad minim veniam, quis nostrud exercitation ullamco laboris nisi. Eiusmod ad tempor incididunt ut labore et dolore magna aliqua.</p>
    <p class="call">Call Us: <strong>012.345.6789</strong></p>
    <p class="web">www.brightmeadows.com</p>
    <p class="addr">Suite 000, City Name, Country Name 00000<br>info@brightmeadows.com</p>
    <svg class="swoosh" width="251" height="190" viewBox="0 0 251 190">
      <path d="M0 30 C90 0 190 10 251 44 L251 60 C190 30 90 26 0 50 Z" fill="var(--green)"/>
    </svg>
    <div class="photo" role="img" aria-label="Photo of a client receiving a shoulder massage"></div>
  </section>

  <!-- Business card front -->
  <section class="sheet card card-front" aria-label="Business card front">
    <div class="brand-name"><span class="dot"></span>Bright Meadows</div>
    <div class="card-divider"></div>
    <div class="card-person">
      <h4>YOUR NAME</h4>
      <div class="role">DIRECTOR</div>
      <ul>
        <li>012.345.6789</li>
        <li>info@brightmeadows.com</li>
        <li>www.brightmeadows.com</li>
        <li style="margin-top:3px">Suite 000, City name,</li>
        <li>Country name 00000</li>
      </ul>
    </div>
    <svg class="swoosh" width="213" height="40" viewBox="0 0 213 40">
      <path d="M0 14 C80 8 160 12 213 22 L213 40 L0 40 Z" fill="var(--green)"/>
      <path d="M0 6 C90 0 170 6 213 18 L213 22 C160 12 90 8 0 12 Z" fill="var(--brown)"/>
    </svg>
    <div class="card-band-text" style="left:10px;bottom:5px;font-size:10px">Well Being Clinic</div>
  </section>

  <!-- Business card back, option 1 -->
  <section class="sheet card card-back-one" aria-label="Business card back, appointment lines at top">
    <div class="write-lines" style="top:24px"><span></span><span></span><span></span><span></span></div>
    <svg class="swoosh" width="213" height="40" viewBox="0 0 213 40">
      <path d="M0 14 C80 8 160 12 213 22 L213 40 L0 40 Z" fill="var(--green)"/>
      <path d="M0 6 C90 0 170 6 213 18 L213 22 C160 12 90 8 0 12 Z" fill="var(--brown)"/>
    </svg>
    <div class="card-band-text" style="left:60px;bottom:6px;font-size:7px">Well Being Clinic</div>
    <div class="card-band-text" style="left:124px;bottom:5px;font-size:10px">Appointment</div>
  </section>
  <div class="caption" style="left:276px;top:908px">Back option 1</div>

  <!-- Business card back, option 2 -->
  <section class="sheet card card-back-two" aria-label="Business card back, appointment heading at top">
    <svg width="213" height="40" viewBox="0 0 213 40" style="position:absolute;left:0;top:0">
      <path d="M0 0 H213 V12 C150 22 80 26 0 28 Z" fill="var(--green)"/>
      <path d="M0 32 C80 30 150 26 213 14 L213 18 C150 30 80 34 0 36 Z" fill="var(--brown)"/>
    </svg>
    <div class="card-band-text" style="left:12px;top:8px;font-size:7px">Well Being Clinic</div>
    <div class="card-band-text" style="left:74px;top:5px;font-size:10px">Appointment</div>
    <div class="write-lines" style="top:58px;left:16px;width:166px"><span></span><span></span><span></span><span></span></div>
  </section>
  <div class="caption" style="left:520px;top:932px">Back option 2</div>

</div>
</body>
</html>
```